New Business Card for Web Design/Internet Marketing Company

Looking for a great looking new business card. We are a 10 year old web design, internet marketing and website management company that works mostly with small businesses.

Our new card needs to better match the colors and style of our website, be bold, extremely usable and slightly edgy.

Target Market(s)

Small/Medium businesses that have websites

Industry/Entity Type

Internet

Requirements
Must have
• Front and back design, full color, rounded corners please

Must use the colors/style of our website (JPG provided)

INFO FOR CARDS (as readable as possible please)
Mark Lenner
President/CEO
mark@trelvanmedia.example
Phone: 520-381-7459
Toll Free: 866-381-7459
Address: 4315 W. Calloway Ave. Ste. 140, Tucson, AZ 85792

THINGS I WANT TO PROMOTE (if there is room):
1. Our Website - www.trelvanmedia.example

2. Social Media
Twitter: @trelvanmedia
Facebook: www.facebook.com/trelvanmedia

3. Our Services
Web Design
Internet Marketing
Website Management

```html
<!DOCTYPE html>
<html lang="en">
<head>
<meta charset="utf-8">
<title>Trelvan Media – Business Card</title>
<link rel="stylesheet" href="https://fonts.googleapis.com/css2?family=Mulish:wght@400;600;700;800&family=Questrial&display=swap">
<style>
  :root {
    --blue: #0a8ccb;
    --orange: #f3822f;
    --ink: #555555;
    --white: #ffffff;
    --backdrop: #e8e4df;
  }
  * { box-sizing: border-box; margin: 0; padding: 0; }
  html, body { width: 1200px; height: 402px; overflow: hidden; }
  body {
    position: relative;
    background: var(--backdrop);
    font-family: "Questrial", sans-serif;
    color: var(--ink);
  }
  .card {
    position: absolute;
    top: 60px;
    width: 508px;
    height: 294px;
    border-radius: 8px;
    overflow: hidden;
  }

  /* Front */
  .card--front { left: 62px; background: var(--white); }
  .brand {
    position: absolute; left: 44px; top: 40px;
    display: flex; align-items: center; gap: 14px;
  }
  .brand__dot {
    width: 56px; height: 56px; border-radius: 50%;
    background: var(--orange);
  }
  .brand__name {
    font-family: "Mulish", sans-serif;
    font-weight: 800; font-size: 42px; letter-spacing: -0.5px;
    color: var(--blue);
  }
  .address {
    position: absolute; left: 40px; top: 134px;
    font-size: 13px; line-height: 17px;
  }
  .name-band {
    position: absolute; left: 0; right: 0; top: 174px; height: 32px;
    background: var(--blue);
    display: flex; align-items: center; padding-left: 40px;
    color: var(--white);
  }
  .name-band__name { font-family: "Mulish", sans-serif; font-weight: 700; font-size: 17px; }
  .name-band__title { font-size: 12px; margin-left: 6px; padding-top: 3px; }
  .contacts {
    position: absolute; left: 40px; top: 222px;
    list-style: none; font-size: 13px; line-height: 18px;
  }
  .contacts li { display: flex; align-items: center; gap: 5px; }
  .contacts svg { width: 10px; height: 10px; fill: var(--blue); flex: none; }

  /* Back */
  .card--back { left: 628px; background: var(--orange); color: var(--white); text-align: center; }
  .back-brand {
    position: absolute; left: 0; right: 0; top: 70px;
    display: flex; justify-content: center; align-items: center; gap: 10px;
  }
  .back-brand__dot { width: 28px; height: 28px; border-radius: 50%; background: var(--white); }
  .back-brand__name { font-family: "Mulish", sans-serif; font-weight: 800; font-size: 34px; }
  .services-title {
    position: absolute; left: 174px; width: 176px; top: 154px;
    font-family: "Mulish", sans-serif; font-weight: 600; font-size: 21px;
    padding-bottom: 2px; border-bottom: 2px solid var(--white);
  }
  .services {
    position: absolute; left: 0; right: 0; top: 200px;
    font-size: 19px; line-height: 25px;
  }
  .social {
    position: absolute; left: 0; right: 0; top: 265px;
    display: flex; justify-content: center; gap: 36px; font-size: 13px;
  }
  .social span { display: flex; align-items: center; gap: 4px; }
  .social i { width: 11px; height: 11px; background: var(--white); opacity: .85; display: block; }
</style>
</head>
<body>

<section class="card card--front" aria-label="Card front">
  <div class="brand">
    <div class="brand__dot"></div>
    <div class="brand__name">Trelvan Media</div>
  </div>

  <p class="address">4315 W. Calloway Ave. Ste. 140<br>Tucson, AZ 85792</p>

  <div class="name-band">
    <span class="name-band__name">Mark Lenner,</span>
    <span class="name-band__title">President/CEO</span>
  </div>

  <ul class="contacts">
    <li><svg viewBox="0 0 10 10"><path d="M2 0h2l1 3-1.5 1a6 6 0 0 0 2.5 2.5L7 5l3 1v2a2 2 0 0 1-2 2A8 8 0 0 1 0 2a2 2 0 0 1 2-2z"/></svg>520-381-7459</li>
    <li><svg viewBox="0 0 10 10"><path d="M2 0h2l1 3-1.5 1a6 6 0 0 0 2.5 2.5L7 5l3 1v2a2 2 0 0 1-2 2A8 8 0 0 1 0 2a2 2 0 0 1 2-2z"/></svg>866-381-7459</li>
    <li><svg viewBox="0 0 10 10"><path d="M0 2h10v6H0z"/></svg>mark@trelvanmedia.example</li>
    <li><svg viewBox="0 0 10 10"><circle cx="5" cy="5" r="5"/></svg>www.trelvanmedia.example</li>
  </ul>
</section>

<section class="card card--back" aria-label="Card back">
  <div class="back-brand">
    <div class="back-brand__dot"></div>
    <div class="back-brand__name">Trelvan Media</div>
  </div>
  <h2 class="services-title">Our Services</h2>
  <p class="services">Web Design &nbsp;•&nbsp; Internet Marketing<br>Website Management</p>
  <div class="social">
    <span><i></i>@trelvanmedia</span>
    <span><i></i>trelvanmedia</span>
  </div>
</section>

</body>
</html>
```